Business Card Design

Business Card for professional consulting firm working with large financial institutions.

Target Market(s)

Executive buyers

Industry/Entity Type

Banking

Contact Information for Business Card

Mild creativity wanted. Not boring, but do elaborate artwork.

Font styles to use
Serif
Sans Serif

Colors

Designer to choose colors to be used in the design.

Requirements
Must have
• Standard business card features - company name, individual name, telephone, website, email, locations.
Nice to have
• Two colors
Should not have
• too many colors, fancy printing, cartoons.

```html
<!DOCTYPE html>
<html lang="en">
<head>
<meta charset="utf-8">
<title>Kestrelbay Business Card</title>
<link rel="stylesheet" href="https://fonts.googleapis.com/css2?family=Crimson+Text:wght@400&family=Work+Sans:wght@400;500&display=swap">
<style>
  :root {
    --backdrop: #232323;
    --card-dark: #161616;
    --card-light: #2c2c2c;
    --silver: #d2d2d2;
    --silver-soft: #bdbdbd;
    --rule: #cfcfcf;
  }
  * { margin: 0; padding: 0; box-sizing: border-box; }
  html, body {
    width: 1200px; height: 900px; overflow: hidden;
    background: var(--backdrop);
  }
  .canvas {
    position: relative; width: 1200px; height: 900px;
    display: flex; flex-direction: column; align-items: center; justify-content: center; gap: 40px;
  }
  .card {
    position: relative; width: 700px; height: 400px;
    background: linear-gradient(135deg, var(--card-dark) 0%, var(--card-light) 70%, #242424 100%);
    box-shadow: 0 14px 30px rgba(0,0,0,0.45);
  }
  .wordmark {
    display: flex; align-items: center; gap: 12px;
    font-family: "Crimson Text", Georgia, serif;
    font-weight: 400; color: var(--silver);
    letter-spacing: 0.5px;
  }
  .wordmark .dot {
    width: 12px; height: 12px; border-radius: 50%; background: var(--silver);
  }
  .card-front .wordmark {
    position: absolute; left: 50%; top: 50%; transform: translate(-50%, -50%);
    font-size: 48px;
  }
  .card-back .wordmark {
    position: absolute; left: 60px; top: 50%; transform: translateY(-50%);
    font-size: 38px;
  }
  .divider {
    position: absolute; left: 345px; top: 105px; width: 2px; height: 190px;
    background: var(--rule);
  }
  .contact {
    position: absolute; left: 380px; top: 108px;
    font-family: "Work Sans", Arial, sans-serif; color: var(--silver-soft);
  }
  .contact .name {
    font-size: 27px; font-weight: 500; letter-spacing: 0.5px; color: var(--silver);
    text-transform: uppercase; line-height: 1;
  }
  .contact .role { font-size: 15px; margin-top: 4px; }
  .contact .address { font-size: 16px; line-height: 1.4; margin-top: 14px; }
  .contact .lines { list-style: none; margin-top: 12px; font-size: 16px; line-height: 1.45; }
  .contact .lines li { display: flex; align-items: center; gap: 10px; }
  .contact .lines svg { width: 12px; height: 12px; flex: none; }
</style>
</head>
<body>
<main class="canvas">
  <section class="card card-front">
    <div class="wordmark"><span class="dot"></span><span>Kestrelbay</span></div>
  </section>

  <section class="card card-back">
    <div class="wordmark"><span class="dot"></span><span>Kestrelbay</span></div>
    <div class="divider"></div>
    <div class="contact">
      <p class="name">Daniel Hart</p>
      <p class="role">Director</p>
      <p class="address">48 Keller Lane,<br>Marlow VIC 3712</p>
      <ul class="lines">
        <li>
          <svg viewBox="0 0 12 12" fill="none" stroke="#bdbdbd" stroke-width="1.2"><path d="M3 1.5 L4.6 4 L3.6 5 Q4.8 7.4 7 8.4 L8 7.4 L10.5 9 L9.5 10.5 Q3.5 10 1.5 2.5 Z"/></svg>
          <span>+330 2417-5063</span>
        </li>
        <li>
          <svg viewBox="0 0 12 12" fill="none" stroke="#bdbdbd" stroke-width="1.2"><rect x="1" y="2.5" width="10" height="7"/><path d="M1 2.5 L6 6.5 L11 2.5"/></svg>
          <span>info@kestrelbay.com</span>
        </li>
        <li>
          <svg viewBox="0 0 12 12" fill="none" stroke="#bdbdbd" stroke-width="1.1"><circle cx="6" cy="6" r="5"/><ellipse cx="6" cy="6" rx="2.2" ry="5"/><path d="M1 6 H11"/></svg>
          <span>www.kestrelbay.com</span>
        </li>
      </ul>
    </div>
  </section>
</main>
</body>
</html>
```